Wordpress website for a new Podcast

Hi, We are looking for a designer to create a wordpress website project for a new podcast and publish it on the domain we own.

The show is called “Bright Gatherings” (logo included) and its aim is to interview guests who work as professional facilitators, trainers, teachers and coaches. The show has a positive vibe, is fun, vibrant and full of positive energy. These are the feelings we want to convey in the design.

The website should have a similar structure to: https://www.plumvesselcast.example/ with the following content:

1) The main page including:
- navigation bar and social buttons at the top
- main graphic design featuring the latest episode
- "latest episodes" section displaying 3 episodes (please design a mask to be used for new episodes when they air together with the face of the interviewee) -> this will link to the respective episodes
- please design an "bright gatherings" book cover mockup to be inluded as a banner -> this will link to Orindel
- subscribe to the newsletter - a banner capturing the name and email of the user -> to be connected to PostWren.
-> a working episode search.

2) Episodes page
- the show will be divided into seasons (12 episodes each) and each episode will need a separate "blog entry" including:
-> A short article (4-5 paragraphs) + stock image
-> interviewee's bio and social links

3) Meet the hosts page
- including bios of the two hosts of the show
- links to their social profiles
- a "request speaker availability" form which sends an email

Some additional nice-to-haves:
1) Good and clean Bio's would be awesome (both for the hosts & the interviewees),
2) an easily navigable episode system,
3) a keyword/date search option
4) easy to share options (share to WhatsApp, Facebook, Twitter, LinkedIn) 5) We must be able to track how the podcasts are shared (google analytics?)

```html
<!DOCTYPE html>
<html lang="en">
<head>
<meta charset="utf-8">
<title>Bright Gatherings — Podcast</title>
<link href="https://fonts.googleapis.com/css2?family=Source+Sans+3:wght@400;600;700&family=Montserrat:wght@700;800&family=Ubuntu:wght@500;700&display=swap" rel="stylesheet">
<style>
:root{
  --orange:#fb5200;
  --orange-2:#ff7a00;
  --yellow:#f9dc23;
  --ink:#1d1d1d;
  --grey:#5a5a5a;
  --muted:#777;
  --panel:#efefef;
  --white:#fff;
}
*{box-sizing:border-box;margin:0;padding:0}
html,body{width:1200px;height:3371px;overflow:hidden;background:var(--white)}
body{position:relative;font-family:"Source Sans 3",Arial,sans-serif;color:var(--ink)}
.abs{position:absolute}
/* top bar */
.topbar{left:0;top:0;width:1200px;height:56px;background:var(--orange)}
.social-top{left:190px;top:20px;display:flex;gap:38px}
.social-top span{width:14px;height:14px;border-radius:50%;background:var(--white);display:block}
.search{left:902px;top:9px;width:184px;height:42px;display:flex}
.search .field{flex:1;background:var(--white);font-size:17px;color:#333;padding:10px 18px}
.search .btn{width:66px;background:var(--yellow);display:flex;align-items:center;justify-content:center}
.nav{left:0;top:56px;width:1200px;height:62px;background:var(--white)}
.nav a{position:absolute;top:20px;font-size:18px;color:var(--ink);text-decoration:none}
.nav .sep{position:absolute;top:14px;width:1px;height:34px;background:#e3e3e3}
.brand{left:488px;top:0;width:161px;height:139px;background:linear-gradient(180deg,var(--orange) 0%,var(--orange-2) 55%,#ffae00 100%);display:flex;align-items:center;justify-content:center;text-align:center;gap:6px;flex-direction:column}
.brand .name{font-family:"Montserrat",sans-serif;font-weight:800;color:var(--white);font-size:19px;line-height:1.1;text-transform:uppercase}
.brand .dot{width:12px;height:12px;background:var(--white)}
/* hero */
.hero{left:0;top:118px;width:1200px;height:556px;background:var(--yellow)}
.hero-book{left:105px;top:209px;width:346px;height:432px}
.hero-title1{left:0;width:1360px;top:245px;text-align:center;font-family:"Montserrat",sans-serif;font-weight:800;color:var(--white);font-size:52px;letter-spacing:9px}
.hero-title2{left:0;width:1360px;top:312px;text-align:center;font-family:"Montserrat",sans-serif;font-weight:800;color:var(--ink);font-size:54px;letter-spacing:-1px}
.hero-text{left:470px;width:420px;top:389px;text-align:center;font-size:13px;line-height:24px;color:var(--ink)}
.btn-white{height:55px;background:var(--white);color:var(--orange);font-weight:700;font-size:18px;display:flex;align-items:center;justify-content:center;letter-spacing:-.3px}
.dots{left:578px;top:623px;display:flex;gap:5px}
.dots span{width:11px;height:11px;border-radius:50%;background:var(--ink)}
.dots span.off{background:transparent;border:1.5px solid var(--ink)}
/* headings */
.sec-title{left:0;width:1200px;text-align:center;font-weight:700;font-size:48px;color:var(--grey);letter-spacing:-1px}
.sec-title em{font-style:normal;color:var(--orange);margin-left:10px}
/* episodes */
.ep{width:324px;height:432px;background:var(--white);box-shadow:0 2px 5px rgba(0,0,0,.25)}
.ep svg{position:absolute;left:0;top:0}
.ep .pin{position:absolute;left:137px;top:143px;width:40px;height:40px;border-radius:50%;background:var(--white);border:2px solid #f2c7b6;display:flex;align-items:center;justify-content:center}
.ep .pin i{width:16px;height:16px;border-radius:50%;border:3px solid var(--orange)}
.ep .num{position:absolute;top:200px;width:100%;text-align:center;color:var(--orange);font-size:19px}
.ep .title{position:absolute;top:234px;width:100%;text-align:center;font-size:15px;line-height:23px;color:var(--ink);letter-spacing:-.3px}
.ep .desc{position:absolute;top:290px;left:28px;right:28px;text-align:center;font-size:13.5px;line-height:21px;color:#444;letter-spacing:-.3px}
.ep .explore{position:absolute;left:0;bottom:0;width:100%;height:51px;background:var(--orange);color:var(--white);font-weight:600;font-size:20px;display:flex;align-items:center;justify-content:center}
/* about */
.about{left:0;top:1396px;width:1200px;height:656px;background:var(--panel)}
.about-title{left:141px;top:1525px;font-weight:700;font-size:52px;color:var(--grey);letter-spacing:-1.5px}
.about-title em{font-style:normal;color:var(--orange)}
.about-text{left:139px;top:1600px;width:561px;font-size:15px;line-height:30px;color:#555;text-align:justify;letter-spacing:-.3px}
.book{background:linear-gradient(160deg,#ff4d00 0%,#ff7a00 55%,#ffb400 100%)}
/* blog */
.post{width:310px;height:450px;border:1.5px solid #f59b74;background:var(--white)}
.post .img{position:absolute;left:0;top:0;width:100%;height:195px}
.post .date{position:absolute;left:6px;top:216px;width:39px;height:41px;background:var(--orange);color:var(--white);font-size:13px;line-height:14px;text-align:center;padding-top:6px}
.post .head{position:absolute;left:56px;top:215px;right:10px;font-size:20px;line-height:26px;color:#333;font-weight:600;letter-spacing:-.2px}
.post .desc{position:absolute;left:20px;right:20px;top:288px;text-align:center;font-size:14.5px;line-height:26px;color:#555}
.post .more{position:absolute;left:84px;top:384px;width:141px;height:44px;border:2px solid var(--orange);display:flex;align-items:center;justify-content:center;font-size:16px;color:#333;letter-spacing:.5px}
/* newsletter & footer */
.footer-frame{left:98px;top:2927px;width:999px;height:376px;border:2px solid var(--orange)}
.news{left:289px;top:2769px;width:618px;height:274px;background:var(--orange);box-shadow:0 12px 30px rgba(80,200,210,.35);text-align:center;color:var(--white)}
.news h3{position:absolute;top:60px;width:100%;font-family:"Ubuntu",sans-serif;font-weight:700;font-size:28px;letter-spacing:.3px}
.news p{position:absolute;top:102px;width:100%;font-size:15px}
.news .input{position:absolute;left:93px;top:153px;width:432px;height:42px;border-radius:21px;background:var(--white);color:#aaa;font-size:11px;text-align:left;padding:13px 20px}
.news .sub{position:absolute;left:389px;top:0;width:136px;height:42px;border-radius:21px;background:var(--yellow);color:var(--ink);font-weight:700;font-size:12px;display:flex;align-items:center;justify-content:center}
.f-logo{left:120px;top:3099px;width:173px;height:171px}
.f-col h4{font-size:14px;font-weight:600;letter-spacing:1.5px;color:#333;margin-bottom:22px}
.f-col p{font-size:13px;color:#666;height:36px}
.f-contact p{font-size:13px;color:#666}
.ic{display:inline-block;vertical-align:middle;margin-right:8px}
.f-social{display:flex;gap:16px}
.f-social span{width:13px;height:13px;border-radius:50%;background:#b8b8b8;display:block}
.copy{left:0;width:1035px;top:3322px;text-align:center;font-size:13.5px;color:#666}
</style>
</head>
<body>

<header>
  <div class="abs topbar"></div>
  <nav class="abs social-top" aria-label="Social links"><span></span><span></span><span></span><span></span><span></span></nav>
  <div class="abs search">
    <div class="field">Search</div>
    <div class="btn"><svg width="26" height="26" viewBox="0 0 26 26"><circle cx="10" cy="10" r="7.5" fill="none" stroke="#1d1d1d" stroke-width="3"/><line x1="15.5" y1="15.5" x2="23" y2="23" stroke="#1d1d1d" stroke-width="3.5" stroke-linecap="round"/></svg></div>
  </div>
  <div class="abs nav">
    <a style="left:213px">Home</a><span class="sep" style="left:280px"></span>
    <a style="left:301px">About</a><span class="sep" style="left:368px"></span>
    <a style="left:386px">Episodes</a>
    <a style="left:683px">Meet The Hosts</a><span class="sep" style="left:815px"></span>
    <a style="left:834px">Podcasts</a><span class="sep" style="left:920px"></span>
    <a style="left:938px">Contact Us</a>
  </div>
  <div class="abs brand"><span class="dot"></span><span class="name">Bright<br>Gatherings</span></div>
</header>

<section>
  <div class="abs hero" role="img" aria-label="Yellow background with a pattern of sketched books"></div>
  <svg class="abs hero-book" viewBox="0 0 346 432" role="img" aria-label="Bright Gatherings book standing on a white round pedestal">
    <defs>
      <linearGradient id="bk" x1="0" y1="0" x2=".4" y2="1"><stop offset="0" stop-color="#ff4d00"/><stop offset=".6" stop-color="#ff7a00"/><stop offset="1" stop-color="#ffb000"/></linearGradient>
      <linearGradient id="pd" x1="0" y1="0" x2="0" y2="1"><stop offset="0" stop-color="#f4f4f4"/><stop offset="1" stop-color="#bdbdbd"/></linearGradient>
    </defs>
    <ellipse cx="173" cy="385" rx="172" ry="45" fill="url(#pd)"/>
    <ellipse cx="173" cy="365" rx="150" ry="34" fill="#f7f7f7"/>
    <polygon points="250,5 285,15 285,380 250,372" fill="#d9d9d9"/>
    <polygon points="75,15 265,0 265,365 75,360" fill="url(#bk)"/>
  </svg>
  <div class="abs hero-title1">BRIGHT</div>
  <div class="abs hero-title2">GATHERINGS</div>
  <p class="abs hero-text">Lorem ipsum dolor sit amet, consectetur adipiscing elit, sed do eiusmod tempor incididunt ut labore et dolore magna aliqua.</p>
  <div class="abs btn-white" style="left:487px;top:459px;width:169px">Get the Book Now</div>
  <div class="abs btn-white" style="left:675px;top:459px;width:169px">Get Trained</div>
  <div class="abs dots"><span></span><span></span><span class="off"></span></div>
</section>

<section>
  <h2 class="abs sec-title" style="top:738px">Latest<em>Podcast Episodes</em></h2>

  <article class="abs ep" style="left:75px;top:874px">
    <svg width="324" height="184" viewBox="0 0 324 184">
      <polygon points="0,0 160,20 160,184 0,184" fill="#ff6200"/>
      <polygon points="160,20 324,0 324,184 160,184" fill="#c9cfd6" role="img" aria-label="Portrait photo of the guest"/>
      <text x="80" y="100" text-anchor="middle" font-family="Montserrat,sans-serif" font-weight="800" font-size="17" fill="#fff">BRIGHT</text>
      <text x="80" y="122" text-anchor="middle" font-family="Montserrat,sans-serif" font-weight="800" font-size="17" fill="#fff">GATHERINGS</text>
    </svg>
    <div class="pin"><i></i></div>
    <div class="num">Episode 195</div>
    <div class="title">Stop Apologizing for<br>Your Core Focus | Mara Lindqvist</div>
    <p class="desc">Do you ever feel guilty because you're not perfectly prioritizing Your Core Focus, or because you're not as successful as you'd like to be?</p>
    <div class="explore">Explore</div>
  </article>

  <article class="abs ep" style="left:441px;top:874px">
    <svg width="324" height="184" viewBox="0 0 324 184">
      <polygon points="0,0 160,20 160,184 0,184" fill="#ff6200"/>
      <polygon points="160,20 324,0 324,184 160,184" fill="#9fa99a" role="img" aria-label="Portrait photo of the guest in a classroom"/>
      <text x="80" y="100" text-anchor="middle" font-family="Montserrat,sans-serif" font-weight="800" font-size="17" fill="#fff">BRIGHT</text>
      <text x="80" y="122" text-anchor="middle" font-family="Montserrat,sans-serif" font-weight="800" font-size="17" fill="#fff">GATHERINGS</text>
    </svg>
    <div class="pin"><i></i></div>
    <div class="num">Episode 194</div>
    <div class="title">Demystifying What It Means to Live<br>The Core Focus | Tessa Corwin</div>
    <p class="desc">Do you ever feel guilty because you're not perfectly prioritizing Your Core Focus, or because you're not as successful as you'd like to be?</p>
    <div class="explore">Explore</div>
  </article>

  <article class="abs ep" style="left:800px;top:874px">
    <svg width="324" height="184" viewBox="0 0 324 184">
      <polygon points="0,0 160,20 160,184 0,184" fill="#ff6200"/>
      <polygon points="160,20 324,0 324,184 160,184" fill="#b8b2a6" role="img" aria-label="Portrait photo of the guest"/>
      <text x="80" y="100" text-anchor="middle" font-family="Montserrat,sans-serif" font-weight="800" font-size="17" fill="#fff">BRIGHT</text>
      <text x="80" y="122" text-anchor="middle" font-family="Montserrat,sans-serif" font-weight="800" font-size="17" fill="#fff">GATHERINGS</text>
    </svg>
    <div class="pin"><i></i></div>
    <div class="num">Episode 193</div>
    <div class="title">Find Your Focus, Cut Your Stress |<br>Dev Halloran</div>
    <p class="desc">Do you ever feel guilty because you're not perfectly prioritizing Your Core Focus, or because you're not as successful as you'd like to be?</p>
    <div class="explore">Explore</div>
  </article>
</section>

<section>
  <div class="abs about"></div>
  <svg class="abs" style="left:210px;top:1461px" width="702" height="536" viewBox="0 0 702 536">
    <g fill="none" stroke="#fb5200" stroke-width="1.5" stroke-dasharray="6 4">
      <polyline points="4,60 4,3 698,3 698,20"/>
      <polyline points="4,480 4,532 698,532 698,510"/>
    </g>
  </svg>
  <h2 class="abs about-title">About <em>Us</em></h2>
  <p class="abs about-text">Lorem ipsum dolor sit amet, consectetur adipiscing elit, sed do eiusmod tempor incididunt ut labore et dolore magna aliqua. Quis ipsum suspendisse ultrices gravida. Risus commodo viverra maecenas accumsan lacus vel facilisis. Lorem ipsum dolor sit amet, consectetur adipiscing elit, sed do eiusmod tempor incididunt ut labore et dolore magna aliqua. Quis ipsum suspendisse ultrices gravida. Risus commodo viverra maecenas accumsan lacus vel facilisis. Lorem ipsum dolor sit amet, consectetur adipiscing elit, sed do eiusmod tempor incididunt ut labore et dolore magna aliqua. Quis ipsum suspendisse ultrices gravida. Risus commodo viverra maecenas accumsan lacus vel facilisis. Lorem ipsum dolor sit amet, consectetur adipiscing elit, sed do eiusmod tempor incididunt ut labore et dolore magna aliqua. Quis ipsum suspendisse ultrices gravida. Risus commodo viverra maecenas accumsan lacus vel facilisis.</p>
  <svg class="abs" style="left:766px;top:1476px" width="294" height="503" viewBox="0 0 294 503" role="img" aria-label="Bright Gatherings book cover mockup">
    <defs><linearGradient id="bk2" x1="0" y1="0" x2=".5" y2="1"><stop offset="0" stop-color="#ff4d00"/><stop offset=".6" stop-color="#ff7a00"/><stop offset="1" stop-color="#ffb000"/></linearGradient></defs>
    <polygon points="262,0 294,14 294,490 262,503" fill="#d6d6d6"/>
    <polygon points="0,20 268,0 268,503 0,487" fill="url(#bk2)"/>
  </svg>
</section>

<section>
  <h2 class="abs sec-title" style="top:2140px">Our<em>Blog</em></h2>

  <article class="abs post" style="left:110px;top:2239px">
    <div class="img" role="img" aria-label="Coin-operated telescope overlooking a city and river" style="background:linear-gradient(180deg,#b9c4c8,#7d8a86)"></div>
    <div class="date">25<br>Jun</div>
    <h3 class="head">Sed ut perspiciatis unde omnis iste natus error sit</h3>
    <p class="desc">Lorem ipsum dolor sit amet, consectetur adipisicing elit, sed do eiusmod tempor incididunt ut labore et dolore.</p>
    <div class="more">READ MORE</div>
  </article>

  <article class="abs post" style="left:444px;top:2239px">
    <div class="img" role="img" aria-label="Guide cover image of a runner at sunset" style="background:linear-gradient(120deg,#c98a2c,#6a3d12)"></div>
    <div class="date">25<br>Jun</div>
    <h3 class="head">Sed ut perspiciatis unde omnis iste natus error sit</h3>
    <p class="desc">Lorem ipsum dolor sit amet, consectetur adipisicing elit, sed do eiusmod tempor incididunt ut labore et dolore.</p>
    <div class="more">READ MORE</div>
  </article>

  <article class="abs post" style="left:777px;top:2239px">
    <div class="img" role="img" aria-label="Guide cover image of hot air balloons in a blue sky" style="background:linear-gradient(160deg,#2f6fb0,#1b3f75)"></div>
    <div class="date">25<br>Jun</div>
    <h3 class="head">Sed ut perspiciatis unde omnis iste natus error sit</h3>
    <p class="desc">Lorem ipsum dolor sit amet, consectetur adipisicing elit, sed do eiusmod tempor incididunt ut labore et dolore.</p>
    <div class="more">READ MORE</div>
  </article>
</section>

<footer>
  <div class="abs footer-frame"></div>
  <div class="abs news">
    <h3>Signup for Newsletter</h3>
    <p>No contact, no set-up costs, just awesome</p>
    <div class="input">Your email adress<div class="sub">Subscribe</div></div>
  </div>

  <div class="abs f-logo brand" style="left:120px;top:3099px;width:173px;height:171px"><span class="dot"></span><span class="name">Bright<br>Gatherings</span></div>

  <div class="abs f-col" style="left:372px;top:3104px">
    <h4>COMPANY</h4><p>Support</p><p>Terms of Service</p><p>Privacy Policy</p><p>Customers</p>
  </div>
  <div class="abs f-col" style="left:542px;top:3104px">
    <h4>LEARN MORE</h4><p>Support</p><p>Products</p><p>Pricing</p><p>Discounts</p>
  </div>
  <div class="abs f-col f-contact" style="left:730px;top:3104px;width:380px">
    <h4>CONTACT US</h4>
    <p><svg class="ic" width="12" height="12" viewBox="0 0 12 12"><polygon points="0,5 12,0 7,12 6,6" fill="#22a06b"/></svg>Brightwave OÜ Lumi tee 7, Tarrow 10450</p>
    <p style="margin-top:18px"><svg class="ic" width="11" height="11" viewBox="0 0 11 11"><path d="M2 0 L4 3 L3 4.5 Q4.5 7 6.5 8 L8 7 L11 9 L9.5 11 Q3 10 0 1.5 Z" fill="#22a06b"/></svg>5 204 318
      <span style="margin-left:36px"><svg class="ic" width="12" height="9" viewBox="0 0 12 9"><rect width="12" height="9" fill="#22a06b"/><polyline points="0,0 6,5 12,0" fill="none" stroke="#fff" stroke-width="1.2"/></svg>info@brightgatherings.example</span></p>
    <div class="f-social" style="margin-top:36px"><span></span><span></span><span></span><span></span></div>
  </div>

  <p class="abs copy">© 2019 All Rights Reserved | Privacy Policy | Terms and Conditions</p>
</footer>

</body>
</html>
```